Website for Ashcombe Tube Drift

Require a website for a river float in the City of Edmonton. Located on North Saskatchewan River. Will need to be a coded website with incorporated booking system through Fare Harbor software.

Pages include
Home
Pricing
About
FAQ
Contact

Ashcombe Tube Drift is an activity based business that will have customers floating down the North Saskatchewan river in Edmonton AB. The site will have all information needed and a full reservation system. The project was launched to provide people in the Edmonton area a favorite summer activity.

Here are similar websites to reference what our business will be doing and what we are looking for.

mossbankfloatco.com
quillpointpaddles.com

Target Market(s)

Families, Groups, Individuals, Anyone who wants to explore the river

Industry/Entity Type

Activities based business/ Outdoor recreational/ River Float

Coding

Coded - Design and coding required

Number of Pages Required

5+ page

Colors
0054AA
0677BA
7BADD7
CADEEF
E8F1F8
F0912C
F2A743
F7CA91
FBE8D2
FDF5EE

```html
<!DOCTYPE html>
<html lang="en">
<head>
<meta charset="utf-8">
<title>Ashcombe Tube Drift</title>
<link href="https://fonts.googleapis.com/css2?family=Mulish:ital,wght@0,400;0,600;0,700;0,800;0,900;1,700&display=swap" rel="stylesheet">
<style>
:root{
  --blue:#0054AA;
  --blue-mid:#0677BA;
  --blue-soft:#7BADD7;
  --blue-pale:#CADEEF;
  --blue-mist:#E8F1F8;
  --sky:#4CBCE3;
  --sky-pale:#D6F1FB;
  --navy:#0B3F8C;
  --orange:#E35A26;
  --orange-warm:#F0912C;
  --ink:#333;
  --grey:#555;
  --white:#fff;
}
*{box-sizing:border-box;margin:0;padding:0}
html,body{width:1200px;height:3694px;overflow:hidden}
body{position:relative;font-family:'Mulish',sans-serif;color:var(--ink);background:var(--white)}
.abs{position:absolute}
.btn{position:absolute;display:flex;align-items:center;justify-content:center;background:var(--orange);color:#fff;font-weight:700;border-radius:30px;text-transform:uppercase}

/* header */
.brand{left:143px;top:30px;display:flex;align-items:center;gap:12px;width:170px}
.brand-dot{width:46px;height:46px;border-radius:50%;background:var(--sky);flex:none}
.brand-name{font-size:19px;font-weight:800;color:var(--navy);line-height:1.1}
.nav{left:362px;top:66px;display:flex;gap:34px;font-size:13.5px;font-weight:700;color:#222}
.nav-phone{left:780px;top:62px;font-size:19px;color:var(--blue);font-weight:600;display:flex;align-items:center;gap:8px}
.login{left:975px;top:60px;width:80px;height:32px;font-size:12px}

/* hero */
.hero{left:0;top:0;width:1200px;height:640px;background:linear-gradient(180deg,#b9c3c4 0%,#d8b892 28%,#9aa39a 48%,#47603f 70%,#2d4a2b 100%)}
.hero-title{left:0;width:1200px;top:278px;text-align:center;font-size:50px;font-weight:900;color:#fff;text-shadow:0 2px 6px rgba(0,0,0,.45)}
.hero-sub{left:0;width:1200px;top:346px;text-align:center;font-size:22px;font-weight:600;color:#fff;line-height:26px;text-shadow:0 1px 4px rgba(0,0,0,.5)}
.hero-btn{left:528px;top:428px;width:144px;height:48px;font-size:16px}
.slider-dots span{position:absolute;left:1127px;width:6px;height:6px;border-radius:50%;background:#fff}

/* about */
.about-title{left:143px;top:668px;font-size:48px;font-weight:900;color:var(--navy)}
.about-text{left:143px;top:738px;width:438px;font-size:12.7px;line-height:24px;color:var(--grey);text-align:justify}
.about-btn{left:143px;top:1003px;width:145px;height:48px;font-size:16px}
.about-art{left:635px;top:655px;width:490px;height:380px;border-radius:245px 245px 120px 170px;background:radial-gradient(circle at 50% 40%,#9fe0f7,#3aa6dd 55%,#0d57b0 100%);border:6px solid var(--blue)}

/* pricing */
.pricing{left:0;top:1090px;width:1200px;height:746px;background:linear-gradient(160deg,#3a5a33 0%,#6d7c55 30%,#9b9a84 55%,#6b7c7a 75%,#4b5e55 100%)}
.card{background:rgba(245,246,248,.96)}
.card-head{position:absolute;left:0;top:0;width:100%;height:86px}
.card-title{position:absolute;left:0;width:100%;text-align:center;font-weight:900;color:var(--navy)}
.price{left:233px;top:1378px;font-size:48px;font-weight:800;color:var(--orange)}
.price-unit{left:314px;top:1401px;font-size:22px;color:#444}
.price-mini{left:408px;top:1400px;width:95px;height:31px;font-size:10px}
.price-desc{left:180px;top:1467px;width:400px;font-size:13.5px;line-height:22px;color:#444}
.rule{height:1px;background:#d7d7d7}
.perks{font-size:13.5px;color:#222;list-style:none}
.perks li{height:26.6px;display:flex;align-items:center;gap:10px}
.perks li::before{content:"";width:9px;height:9px;border:3px solid var(--sky);border-radius:50%;background:#fff;flex:none}
.price-btn{left:297px;top:1665px;width:144px;height:48px;font-size:16px}
.group{left:185px;top:1750px;font-size:23px;font-weight:600;color:#333}
.group a{color:var(--blue);text-decoration:underline}
.note{left:185px;top:1784px;font-size:14px;color:#555}

/* faq */
.faq-bg{left:0;top:1836px;width:1200px;height:730px;background:linear-gradient(180deg,#fff 0%,#f1f4f7 45%,#e6ecf1 70%,#fff 100%)}
.faq-title{left:0;width:1200px;top:1910px;text-align:center;font-size:50px;font-weight:900;color:var(--navy)}
.faq-item{position:absolute;width:437px;height:44px;border-radius:22px;background:#fff;box-shadow:0 1px 4px rgba(0,0,0,.22);display:flex;align-items:center;padding:0 10px 0 28px;font-size:13.5px;color:#333;line-height:15px}
.faq-item span{flex:1}
.faq-item i{width:29px;height:29px;border-radius:50%;background:var(--blue);color:#fff;font-style:normal;font-size:16px;display:flex;align-items:center;justify-content:center;flex:none}
.faq-item.open{background:var(--sky-pale);color:var(--blue)}
.faq-answer{left:615px;top:2335px;width:430px;font-size:11.5px;line-height:24.6px;color:#444}
.faq-answer b{color:var(--blue);font-weight:600;font-size:13px}

/* contact */
.contact-bg{left:0;top:2560px;width:1200px;height:745px;background:linear-gradient(180deg,#0d2f7e 0%,#1b56b5 35%,#2a6bd0 60%,#1f4da8 100%)}
.contact-card{left:374px;top:2672px;width:452px;height:548px}
.c-line{position:absolute;left:412px;display:flex;align-items:center;gap:14px;font-size:18px;color:#222}
.sq{width:42px;height:42px;border-radius:4px;background:var(--blue)}
.circ{width:42px;height:42px;border-radius:50%;background:#555}
.visit{left:416px;top:2982px;font-size:23px;line-height:27px;color:#333;font-weight:600}
.addr{left:416px;top:3037px;font-size:17px;color:var(--blue);display:flex;gap:6px;align-items:center}
.map{left:404px;top:3073px;width:388px;height:124px;background:linear-gradient(120deg,#eef0ea 0%,#e3eadc 40%,#b9dcf3 50%,#e8ebe4 62%,#f0efe9 100%)}

/* footer */
.footer{left:0;top:3305px;width:1200px;height:389px;background:#0a4aa8;color:#fff}
.f-label{left:145px;top:3354px;font-size:15px;font-weight:600}
.f-connect{left:145px;top:3380px;font-size:21px}
.f-line{position:absolute;left:145px;display:flex;align-items:center;gap:14px;font-size:21px;font-weight:600}
.f-social{left:145px;top:3508px;display:flex;gap:22px;align-items:center}
.f-social .sq,.f-social .circ{background:#fff;width:52px;height:52px}
.f-social .circ{width:42px;height:42px}
.f-float{left:527px;top:3352px;font-size:21px;font-style:italic;font-weight:700}
.f-sign{left:527px;top:3415px;font-size:27px;font-weight:900;line-height:31px}
.f-form{left:530px;top:3510px;width:280px;height:42px;border-radius:21px;background:#fff;color:#666;font-size:13px;display:flex;align-items:center;padding-left:28px}
.f-form .btn{position:absolute;right:0;top:0;width:78px;height:42px;font-size:12px}
.f-brand{left:830px;top:3390px;display:flex;align-items:center;gap:10px;width:150px}
.f-brand .brand-dot{background:#fff;width:40px;height:40px}
.f-brand .brand-name{color:#fff;font-size:17px}
.f-nav{left:1006px;top:3353px;list-style:none;font-size:13.5px;font-weight:700}
.f-nav li{height:33px}
.copy{left:0;width:1200px;top:3634px;text-align:center;font-size:13px}
</style>
</head>
<body>

<!-- hero -->
<div class="abs hero" role="img" aria-label="Photo of downtown Edmonton skyline above the river valley at sunset"></div>
<svg class="abs" style="left:0;top:420px" width="1200" height="230" viewBox="0 0 1200 230">
  <path d="M0 40 C40 90 90 80 150 100 C260 135 360 110 470 130 C560 150 580 175 600 175 C640 175 700 120 820 110 C950 100 1080 110 1140 80 C1170 65 1190 50 1200 30 L1200 230 L0 230Z" fill="#45b6e3"/>
  <path d="M0 70 C40 115 90 105 150 120 C260 150 360 125 470 145 C560 165 580 190 600 190 C640 190 700 140 820 130 C950 120 1080 130 1140 100 C1170 85 1190 70 1200 55 L1200 230 L0 230Z" fill="#fff"/>
</svg>
<div class="abs brand"><span class="brand-dot"></span><span class="brand-name">Ashcombe Tube Drift</span></div>
<nav class="abs nav"><span>HOME</span><span>PRICING</span><span>ABOUT</span><span>FAQ</span><span>CONTACT</span></nav>
<div class="abs nav-phone">
  <svg width="17" height="17" viewBox="0 0 24 24"><path fill="#0054AA" d="M6.6 10.8a15 15 0 006.6 6.6l2.2-2.2c.3-.3.7-.4 1-.2 1.1.4 2.3.6 3.6.6.6 0 1 .4 1 1V20c0 .6-.4 1-1 1C10.6 21 3 13.4 3 4c0-.6.4-1 1-1h3.5c.6 0 1 .4 1 1 0 1.3.2 2.5.6 3.6.1.3 0 .7-.2 1z"/></svg>
  +1 780 555 0142</div>
<div class="btn login">Login</div>
<h1 class="abs hero-title">ASHCOMBE TUBE DRIFT</h1>
<p class="abs hero-sub">Float the North Saskatchewan through<br>downtown Edmonton</p>
<div class="btn hero-btn">Book Now</div>
<div class="slider-dots"><span style="top:376px;background:var(--orange)"></span><span style="top:396px"></span><span style="top:416px"></span></div>
<svg class="abs" style="left:586px;top:590px" width="28" height="50" viewBox="0 0 28 50">
  <rect x="5" y="1" width="18" height="28" rx="9" fill="#fff" stroke="#555" stroke-width="1.5"/>
  <line x1="14" y1="7" x2="14" y2="13" stroke="#555" stroke-width="1.5"/>
  <path d="M9 33l5 5 5-5M9 40l5 5 5-5" fill="none" stroke="#555" stroke-width="1.3"/>
</svg>

<!-- about -->
<h2 class="abs about-title">ABOUT US</h2>
<p class="abs about-text">Float the North Saskatchewan through downtown Edmonton Edmonton's Best Summer Activity.We provide the lifejacket, paddle, river tube and shuttle service. You just have to show up.Ashcombe Tube Drift was launched to provide people in the Edmonton area a favorite summer activity. Nothing is better on a hot summer day, than spending it on the river and seeing Edmonton from a new perspective.Our home base and meeting spot is at Driftwood Landing (Map Link), by the Glasshouse Conservatory. This is where you will check in, and board the shuttle. The shuttle will take all floaters up river to Hollow Pine Boat Launch, where your tube will be waiting.</p>
<div class="btn about-btn">Book Now</div>
<div class="abs about-art" role="img" aria-label="Illustration of a river tube beneath an arched city bridge"></div>

<!-- pricing -->
<div class="abs pricing" role="img" aria-label="Photo of people floating on tubes among river rocks"></div>
<svg class="abs" style="left:0;top:1085px" width="1200" height="160" viewBox="0 0 1200 160">
  <path d="M0 0 H1200 V150 C1000 40 800 10 600 10 C400 10 200 40 0 150Z" fill="#fff"/>
  <path d="M0 150 C200 40 400 10 600 10 C800 10 1000 40 1200 150" fill="none" stroke="#0a3f8e" stroke-width="10"/>
</svg>
<div class="abs card" style="left:143px;top:1290px;width:452px;height:546px">
  <svg class="card-head" viewBox="0 0 452 86" preserveAspectRatio="none">
    <path d="M0 0H452V60C360 95 92 95 0 60Z" fill="#56bde3"/>
    <path d="M0 60C92 95 360 95 452 60" fill="none" stroke="#0a3f8e" stroke-width="3"/>
  </svg>
  <div class="card-title" style="top:20px;font-size:32px">TUBE AND SHUTTLE</div>
</div>
<div class="abs price">$30</div>
<div class="abs price-unit">/person</div>
<div class="btn price-mini">Book Now</div>
<p class="abs price-desc">We keep our pricing simple and include everything you need:<br>Premium comfort float tube with backrest and cup holder</p>
<div class="abs rule" style="left:180px;top:1518px;width:380px"></div>
<ul class="abs perks" style="left:187px;top:1543px"><li>Lifejacket</li><li>Paddle</li><li>Round trip shuttle service</li><li>Safety training</li></ul>
<ul class="abs perks" style="left:427px;top:1543px"><li>Staff assistance</li><li>Parking</li><li>Unlimited Fun!</li></ul>
<div class="btn price-btn">Book Now</div>
<div class="abs rule" style="left:180px;top:1733px;width:380px"></div>
<div class="abs group">Group of 10 or more? <a>Contact us</a></div>
<div class="abs note">*does not include taxes or fees</div>

<!-- faq -->
<div class="abs faq-bg" role="img" aria-label="Faint photo of the Edmonton skyline"></div>
<h2 class="abs faq-title">FAQ</h2>
<div class="faq-item" style="left:150px;top:2018px"><span>How do I reserve my float?</span><i>+</i></div>
<div class="faq-item" style="left:150px;top:2069px"><span>What is included?</span><i>+</i></div>
<div class="faq-item" style="left:150px;top:2121px"><span>Where are you located?</span><i>+</i></div>
<div class="faq-item" style="left:150px;top:2173px"><span>Where should I park?</span><i>+</i></div>
<div class="faq-item" style="left:150px;top:2224px"><span>What happens if I miss my shuttle?</span><i>+</i></div>
<div class="faq-item" style="left:150px;top:2276px"><span>Are lifejackets required?</span><i>+</i></div>
<div class="faq-item" style="left:150px;top:2327px"><span>What are the terms and conditions?</span><i>+</i></div>
<div class="faq-item" style="left:150px;top:2379px"><span>What happens if I miss the exit point?</span><i>+</i></div>
<div class="faq-item" style="left:150px;top:2430px"><span>What safety information should I know?</span><i>+</i></div>
<div class="faq-item" style="left:597px;top:2018px"><span>What should I bring?</span><i>+</i></div>
<div class="faq-item" style="left:597px;top:2069px"><span>What time should I arrive?</span><i>+</i></div>
<div class="faq-item" style="left:597px;top:2121px"><span>How long does the trip take?</span><i>+</i></div>
<div class="faq-item" style="left:597px;top:2173px"><span>How do I complete the waiver?</span><i>+</i></div>
<div class="faq-item" style="left:597px;top:2224px"><span>What do I do if there is bad weather on the<br>day of booking?</span><i>+</i></div>
<div class="faq-item open" style="left:597px;top:2276px"><span>What is your cancellation policy?</span><i>-</i></div>
<p class="abs faq-answer">We have a 48-hour cancellation policy. Those canceling 48 hours prior to their reservation will receive a full refund. Those canceling under 48 hours prior to their reservation will receive a credit that can be used at a later date. "No Shows" will be charged the full rental rate.<br>To cancel, please email <b>info@ashcombetubedrift.com or call us</b></p>

<!-- contact -->
<div class="abs contact-bg" role="img" aria-label="Blue-toned photo of an arched bridge over the river and city skyline"></div>
<svg class="abs" style="left:0;top:2555px" width="1200" height="150" viewBox="0 0 1200 150">
  <path d="M0 0H1200V140C1000 35 800 10 600 10C400 10 200 35 0 140Z" fill="#fff"/>
  <path d="M0 140C200 35 400 10 600 10C800 10 1000 35 1200 140" fill="none" stroke="#0a3f8e" stroke-width="10"/>
</svg>
<div class="abs card contact-card">
  <svg class="card-head" viewBox="0 0 452 86" preserveAspectRatio="none">
    <path d="M0 0H452V55C360 90 92 90 0 55Z" fill="#56bde3"/>
    <path d="M0 55C92 90 360 90 452 55" fill="none" stroke="#0a3f8e" stroke-width="3"/>
  </svg>
  <div class="card-title" style="top:18px;font-size:32px">CONTACT US</div>
</div>
<div class="c-line" style="top:2794px;font-size:17px;color:#444">We'd love to hear from you!</div>
<div class="c-line" style="top:2838px">
  <svg width="18" height="18" viewBox="0 0 24 24"><path fill="#4CBCE3" d="M6.6 10.8a15 15 0 006.6 6.6l2.2-2.2c.3-.3.7-.4 1-.2 1.1.4 2.3.6 3.6.6.6 0 1 .4 1 1V20c0 .6-.4 1-1 1C10.6 21 3 13.4 3 4c0-.6.4-1 1-1h3.5c.6 0 1 .4 1 1 0 1.3.2 2.5.6 3.6.1.3 0 .7-.2 1z"/></svg>+1 780 555 0142</div>
<div class="c-line" style="top:2864px">
  <svg width="18" height="14" viewBox="0 0 18 14"><rect width="18" height="14" rx="2" fill="#4CBCE3"/><path d="M1 2l8 6 8-6" fill="none" stroke="#fff" stroke-width="1.5"/></svg>info@ashcombetubedrift.com</div>
<div class="c-line" style="top:2913px;gap:16px"><span class="sq"></span><span class="sq" style="background:#d9387a"></span><span class="circ"></span></div>
<div class="abs visit">Come visit us on float days at<br>Driftwood Landing</div>
<div class="abs addr">
  <svg width="18" height="15" viewBox="0 0 18 15"><path d="M1 2l5-1.5 6 1.5 5-1.5v12l-5 1.5-6-1.5-5 1.5z" fill="none" stroke="#0054AA" stroke-width="1.6"/></svg>1420 Riverbend Rd NW, Edmonton, AB</div>
<div class="abs map" role="img" aria-label="Street map showing the river and the landing location"></div>

<!-- footer -->
<footer class="abs footer"></footer>
<div class="abs f-label" style="color:#fff">ASHCOMBE TUBE DRIFT</div>
<div class="abs f-connect" style="color:#fff">CONNECT</div>
<div class="f-line" style="top:3409px;color:#fff">
  <svg width="20" height="15" viewBox="0 0 18 14"><rect width="18" height="14" rx="2" fill="#fff"/><path d="M1 2l8 6 8-6" fill="none" stroke="#0a4aa8" stroke-width="1.5"/></svg>info@ashcombetubedrift.com</div>
<div class="f-line" style="top:3441px;color:#fff">
  <svg width="22" height="17" viewBox="0 0 18 15"><path d="M1 2l5-1.5 6 1.5 5-1.5v12l-5 1.5-6-1.5-5 1.5z" fill="#fff"/></svg>Driftwood Landing</div>
<div class="abs f-social"><span class="sq"></span><span class="sq"></span><span class="circ"></span></div>
<div class="abs f-float" style="color:#fff">Floating 7 days a week</div>
<div class="abs f-sign" style="color:#fff">SIGN UP FOR OUR<br>MAILING LIST</div>
<div class="abs f-form">Enter Email<div class="btn">Sign Up</div></div>
<div class="abs f-brand"><span class="brand-dot"></span><span class="brand-name">Ashcombe Tube Drift</span></div>
<ul class="abs f-nav" style="color:#fff"><li>Home</li><li>Pricing</li><li>About</li><li>FAQ</li><li>Contact</li></ul>
<div class="abs copy" style="color:#fff">© 2022 Ashcombe Tube Drift. All rights reserved &nbsp;|&nbsp; Privacy &nbsp;|&nbsp; Terms of Use</div>

</body>
</html>
```